Sales and Marketing company needs website page graphics

We are redesigning our website and need graphics for the top of our solution pages. Currently you’ll see that there is one photo graphic with a differing color screen for each section. We’re looking for photo graphic designs that will represent each unique solution section (lead generation, prospecting, hiring) and fit within the overall website design. We will add the section title text to the photo graphic. This will be a total of 3 graphics.

This is a link to the working website redesign: http://trevindale.com/brunexatemp/
The content on the working redesign page is correct and will give you a good sense for how we talk about each solution. You’ll notice that the redesign is text heavy. We’ll work on that next.

Our current website is: www.brunexa.com
You’ll get a good sense for our designs on our blog: http://www.brunexa.com/blog

As a company, our goal is to help our clients get more customers. We do that through consulting, training and outsourced lead generation. Key words that describe us: flexible, responsive, and fun. (Although you don’t see that in our current website, hopefully it comes through more on our blog – and then on our new website!)

We will need the graphic design in high resolution formats. We will own the copyright and intellectual property.

North American companies that earn $750K - $85M in annual revenue selling to other businesses. Most are in the computer technology industry.

Business Service

Sans Serif

• Fit the design of the website.
• If there are people in the graphics, I like to see diversity: Asian,Black, Latin, Caucasian, men and women.
• Be creative, not like every other graphic you see on a website. We are a woman owned business and Marisol is well known. We don't want to feel generic. Potentially be something we can use elements of for other graphics.
• We really want your expertise and this is our first project with Artvoyle .
• We will insert the solution section text, so there wouldn't be the text unless it's part of the graphic design.

```html
<!DOCTYPE html>
<html lang="en">
<head>
<meta charset="utf-8">
<title>Brunexa Group – Hiring and Onboarding</title>
<link href="https://fonts.googleapis.com/css2?family=Lato:wght@400;700;900&display=swap" rel="stylesheet">
<style>
  :root {
    --purple: #5b3a8f;
    --purple-deep: #4a2f78;
    --green: #8cc63f;
    --teal: #1f6b73;
    --grey: #8e8e8e;
    --grey-light: #c9c9c9;
    --ink: #333333;
    --paper: #ffffff;
    --bar: #f1f1f1;
  }
  * { box-sizing: border-box; margin: 0; padding: 0; }
  html, body { width: 1200px; height: 757px; overflow: hidden; background: var(--paper); }
  body { font-family: "Lato", Arial, sans-serif; color: var(--ink); position: relative; }

  .address-bar {
    height: 24px; background: var(--bar); border-bottom: 1px solid #dcdcdc;
    font-size: 11px; color: #777; padding: 5px 16px;
  }
  .site-header {
    height: 86px; display: flex; align-items: center; padding: 0 70px;
    position: relative;
  }
  .brand { font-size: 44px; font-weight: 900; color: var(--purple); letter-spacing: -1px; }
  .speak-link {
    position: absolute; left: 770px; top: 46px;
    font-size: 12px; font-weight: 700; color: var(--purple); letter-spacing: .5px;
  }
  .phone {
    position: absolute; right: 40px; top: 22px;
    font-size: 20px; color: var(--purple-deep);
  }
  .main-nav {
    height: 30px; background: var(--purple); display: flex; justify-content: flex-end;
    padding-right: 30px;
  }
  .main-nav a {
    color: #fff; text-decoration: none; font-size: 11px; font-weight: 700;
    padding: 0 12px; line-height: 30px; letter-spacing: .3px;
  }
  .main-nav a.is-active { background: var(--green); }

  .hero {
    height: 300px;
    background:
      radial-gradient(ellipse at 40% 20%, rgba(255,255,255,.75), rgba(255,255,255,0) 55%),
      linear-gradient(180deg, #b9aac9 0%, #8f7aa8 45%, #4c3a62 75%, #2c2238 100%);
  }

  .content { display: flex; padding: 22px 40px 0 150px; }
  .system-diagram { width: 260px; flex: none; margin-top: 6px; }
  .copy { padding-left: 48px; }
  .copy h1 {
    font-size: 28px; font-weight: 400; color: var(--purple); line-height: 1.1;
    margin-bottom: 12px;
  }
  .copy p { font-size: 12.5px; line-height: 1.6; margin-bottom: 10px; }
  .copy strong { font-weight: 700; }
  .copy u { text-decoration: underline; }
</style>
</head>
<body>
  <div class="address-bar">brunexa.com/hiring-onboarding/</div>

  <header class="site-header">
    <div class="brand">Brunexa</div>
    <div class="speak-link">HIRE MARISOL TO SPEAK</div>
    <div class="phone">+1 303 555 0148</div>
  </header>

  <nav class="main-nav">
    <a href="#">ABOUT</a>
    <a href="#">WHAT WE DO</a>
    <a href="#">LEAD GENERATION</a>
    <a href="#">PROSPECTING</a>
    <a href="#" class="is-active">HIRING &amp; ONBOARDING</a>
    <a href="#">RESOURCES</a>
    <a href="#">EVENTS</a>
    <a href="#">BLOG</a>
    <a href="#">CONTACT</a>
  </nav>

  <div class="hero" role="img" aria-label="Photo of business people standing around a meeting table, silhouetted against a bright window, purple tinted"></div>

  <section class="content">
    <svg class="system-diagram" viewBox="0 0 260 240" role="img" aria-label="Revenue Generating System diagram">
      <circle cx="130" cy="125" r="88" fill="none" stroke="var(--grey-light)" stroke-width="6"/>
      <text x="130" y="118" text-anchor="middle" font-size="18" fill="var(--grey)" font-family="Lato, sans-serif">Revenue</text>
      <text x="130" y="138" text-anchor="middle" font-size="18" fill="var(--grey)" font-family="Lato, sans-serif">Generating</text>
      <text x="130" y="158" text-anchor="middle" font-size="18" fill="var(--grey)" font-family="Lato, sans-serif">System</text>

      <circle cx="130" cy="42" r="38" fill="var(--grey)" stroke="#fff" stroke-width="3"/>
      <text x="130" y="38" text-anchor="middle" font-size="9" font-weight="700" fill="#fff" font-family="Lato, sans-serif">LEAD</text>
      <text x="130" y="50" text-anchor="middle" font-size="9" font-weight="700" fill="#fff" font-family="Lato, sans-serif">GENERATION</text>

      <circle cx="52" cy="185" r="38" fill="var(--grey)" stroke="#fff" stroke-width="3"/>
      <text x="52" y="189" text-anchor="middle" font-size="9" font-weight="700" fill="#fff" font-family="Lato, sans-serif">PROSPECTING</text>

      <circle cx="208" cy="185" r="38" fill="var(--teal)" stroke="#fff" stroke-width="3"/>
      <text x="208" y="181" text-anchor="middle" font-size="9" font-weight="700" fill="#fff" font-family="Lato, sans-serif">HIRING &amp;</text>
      <text x="208" y="193" text-anchor="middle" font-size="9" font-weight="700" fill="#fff" font-family="Lato, sans-serif">ONBOARDING</text>
    </svg>

    <div class="copy">
      <h1>The Brunexa Group Approach to Sales and Marketing<br>Hiring and Onboarding</h1>
      <p>The average sales person takes between nine to twelve months to reach full productivity. The average marketing person takes three to six months to reach full productivity. These numbers may shock you, but they're simply true.</p>
      <p>Without ensuring that you made the right selection in the hiring process and a well thought out training onboarding plan, <strong>your new sales rep may never reach their full selling potential</strong> – no matter how much sales experience they have. <strong>And your marketing staffer may quit</strong> before they reach their third month.</p>
      <p>But of course, that <u>doesn't</u> mean you have to wait until the worst happens to know if your new hire is going to cut it.</p>
      <p>We are not recruiters. <strong>We guide you through developing and implementing a successful hiring process</strong> to add staff that fit your company culture and get you the sales and lead generation results required to meet your goals.</p>
    </div>
  </section>
</body>
</html>
```